NEW Modern Sleek Business Card for VR Language Startup

Our startup is using VR to lead the next wave of world language education. We need a two-sided business card that introduces the larger organization (Brightloom Language Inc) and our contact info on one side and shows the product, Glimwoorld, on the other side.

Side 1 (contact info)= Brightloom Logo and Contact info (name, title, phone, email)

Side 2 (product)= Glimworld logo, text, and website
Text= Culturally Immersive Language Learning Games
Website= www.glimworld-play.com

Target Market(s)

Education, Technology

Contact Information for Business Card

Contact info will be updated upon approval of the design. For now, put this as a placeholder.

Perry Dunmore
Founder & CEO
pdunmore@quillpost-mail.net
(555)-014-2286

Font styles to use
Other font styles liked:
• Gibson and Century Gothic are the brand fonts

Requirements
Nice to have
• I would love to see cohesion between the design and colors of the two logos. I have attached a few business card designs that I like, so you can get a feel for my preferred style.

```html
<!DOCTYPE html>
<html lang="en">
<head>
<meta charset="utf-8">
<title>Glimworld / Brightloom Business Card</title>
<link href="https://fonts.googleapis.com/css2?family=Montserrat:wght@600;700&family=Questrial&display=swap" rel="stylesheet">
<style>
  :root {
    --stage: #e9e9eb;
    --card: #ffffff;
    --ink: #222226;
    --ink-soft: #4a4a50;
    --violet: #5b3ff0;
    --accent-red: #ef2d4d;
    --band-orange: #f7733a;
    --band-red: #ef2d4d;
    --band-purple: #8e52c4;
    --band-cyan: #1ee3ea;
    --blue-grad-a: #1ee3ea;
    --blue-grad-b: #6a4cf5;
  }
  * { box-sizing: border-box; margin: 0; padding: 0; }
  html, body { width: 1200px; height: 1200px; overflow: hidden; }
  body {
    background: var(--stage);
    font-family: "Questrial", "Century Gothic", sans-serif;
    color: var(--ink);
    position: relative;
  }
  .card {
    position: absolute;
    left: 160px;
    width: 880px;
    height: 503px;
    background: var(--card);
    border-radius: 34px;
    overflow: hidden;
    box-shadow: 0 12px 34px rgba(0,0,0,.18);
  }
  .card--product { top: 70px; }
  .card--contact { top: 627px; }

  /* Product side */
  .product-mark {
    position: absolute;
    left: 50%; top: 110px;
    transform: translateX(-50%);
    display: flex; align-items: center; gap: 18px;
  }
  .product-mark__dot {
    width: 34px; height: 34px; border-radius: 50%;
    background: var(--violet);
  }
  .product-mark__name {
    font-family: "Montserrat", sans-serif;
    font-weight: 600;
    font-size: 74px;
    color: var(--ink-soft);
    letter-spacing: -1px;
  }
  .product-tagline {
    position: absolute;
    top: 232px; width: 100%;
    text-align: center;
    font-size: 26px;
    color: var(--ink-soft);
    letter-spacing: .5px;
  }
  .product-url {
    position: absolute;
    top: 370px; width: 100%;
    text-align: center;
    font-family: "Montserrat", sans-serif;
    font-weight: 700;
    font-size: 24px;
    color: var(--violet);
  }

  /* Contact side */
  .contact-glow {
    position: absolute;
    left: 60px; top: -60px;
    width: 360px; height: 360px;
    border-radius: 50%;
    background: linear-gradient(180deg, rgba(247,115,58,.14), rgba(30,227,234,.14));
  }
  .contact-person {
    position: absolute;
    left: 56px; top: 300px;
  }
  .contact-person__name {
    font-family: "Montserrat", sans-serif;
    font-weight: 700;
    font-size: 38px;
    color: var(--ink);
    display: inline-block;
  }
  .contact-person__title {
    display: inline-block;
    margin-left: 14px;
    font-size: 24px;
    color: var(--ink);
  }
  .contact-lines {
    margin-top: 12px;
    display: flex; gap: 30px;
    font-size: 22px;
  }
  .contact-line { display: flex; align-items: center; gap: 9px; }
  .contact-line svg { width: 20px; height: 20px; }
  .brand-mark {
    position: absolute;
    right: 60px; top: 40px;
    height: 380px;
    display: flex; flex-direction: column; align-items: center; gap: 16px;
  }
  .brand-mark__dot {
    width: 30px; height: 30px; border-radius: 50%;
    background: var(--band-purple);
  }
  .brand-mark__name {
    writing-mode: vertical-rl;
    transform: rotate(180deg);
    font-family: "Montserrat", sans-serif;
    font-weight: 600;
    font-size: 40px;
    letter-spacing: 2px;
    color: var(--ink);
  }
  .color-band {
    position: absolute;
    left: 0; bottom: 0; width: 100%; height: 36px;
    display: flex; gap: 3px;
    background: var(--card);
  }
  .color-band span { flex: 1; }
  .color-band .orange { background: var(--band-orange); }
  .color-band .red { background: var(--band-red); }
  .color-band .purple { background: var(--band-purple); }
  .color-band .cyan { background: var(--band-cyan); }
</style>
</head>
<body>

<section class="card card--product">
  <div class="product-mark">
    <span class="product-mark__dot"></span>
    <span class="product-mark__name">Glimworld</span>
  </div>
  <p class="product-tagline">Culturally Immersive Language Learning Games</p>
  <p class="product-url">www.glimworld-play.com</p>
</section>

<section class="card card--contact">
  <div class="contact-glow"></div>
  <div class="contact-person">
    <h1 class="contact-person__name">PERRY DUNMORE</h1>
    <span class="contact-person__title">President</span>
    <div class="contact-lines">
      <div class="contact-line">
        <svg viewBox="0 0 24 24" aria-hidden="true"><path fill="var(--accent-red)" d="M6.6 10.8a15.1 15.1 0 0 0 6.6 6.6l2.2-2.2c.3-.3.7-.4 1-.2 1.1.4 2.3.6 3.6.6.6 0 1 .4 1 1V20c0 .6-.4 1-1 1A17 17 0 0 1 3 4c0-.6.4-1 1-1h3.5c.6 0 1 .4 1 1 0 1.3.2 2.5.6 3.6.1.3 0 .7-.2 1z"/></svg>
        <span>(555)-014-2286</span>
      </div>
      <div class="contact-line">
        <svg viewBox="0 0 24 24" aria-hidden="true"><rect x="2" y="5" width="20" height="14" rx="2" fill="none" stroke="var(--accent-red)" stroke-width="2"/><path d="M3 6l9 7 9-7" fill="none" stroke="var(--accent-red)" stroke-width="2"/></svg>
        <span>pdunmore@quillpost-mail.net</span>
      </div>
    </div>
  </div>
  <div class="brand-mark">
    <span class="brand-mark__dot"></span>
    <span class="brand-mark__name">Brightloom Language</span>
  </div>
  <div class="color-band">
    <span class="orange"></span><span class="red"></span><span class="purple"></span><span class="cyan"></span>
  </div>
</section>

</body>
</html>
```